Business Card Design

Velora Pixel Outreach

An online marketing consulting & strategy business for the cosmetic niche

We specialise in Increasing Leads, Conversions & Content Marketing

I am looking for a very clean, BOLD business card that is simple & effective

Target Market(s)

cosmetic surgeons & cosmetic clinics

Industry/Entity Type

Marketing

Contact Information for Business Card

Dermot Kalway
Online Marketing Strategist

Dermot@VeloraPixelOutreach.example
0492 158 620

LinkedIn: in/dermotkalway

```html
<!DOCTYPE html>
<html lang="en">
<head>
<meta charset="utf-8">
<title>Velora Pixel Outreach – Business Card</title>
<link rel="stylesheet" href="https://fonts.googleapis.com/css2?family=Open+Sans:wght@400;600;700&display=swap">
<style>
  :root {
    --stage: #ababab;
    --green: #a6ce39;
    --blue: #2fa9df;
    --ink: #5a5a5a;
    --white: #ffffff;
    --faint: rgba(255, 255, 255, 0.22);
    --faint-back: rgba(47, 169, 223, 0.12);
  }
  * { box-sizing: border-box; margin: 0; padding: 0; }
  html, body {
    width: 1200px; height: 900px; overflow: hidden;
    background: var(--stage);
    font-family: "Open Sans", Arial, sans-serif;
  }
  .sheet { position: relative; width: 1200px; height: 900px; }

  .card {
    position: absolute; width: 565px; height: 340px;
    overflow: hidden;
    box-shadow: 3px 4px 5px rgba(0, 0, 0, 0.45);
  }
  .card--rounded { height: 327px; border-radius: 26px; }

  /* Front */
  .card--front { background: linear-gradient(to bottom, var(--green) 0%, #7fc08a 45%, var(--blue) 100%); }
  .front-ring {
    position: absolute; left: -60px; top: 30px;
    width: 380px; height: 380px; border-radius: 50%;
    border: 46px solid var(--faint);
  }
  .front-brand { position: absolute; left: 212px; bottom: 22px; display: flex; align-items: center; gap: 18px; }
  .front-brand .mark { width: 92px; height: 92px; border-radius: 50%; background: var(--white); }
  .front-brand .name {
    color: var(--white); font-weight: 600; font-size: 31px;
    line-height: 1.05; letter-spacing: 3px; text-transform: uppercase;
  }

  /* Back */
  .card--back { background: var(--white); }
  .back-band {
    position: absolute; left: 0; top: 0; bottom: 0; width: 114px;
    background: linear-gradient(to bottom, var(--blue) 0%, var(--blue) 12%, var(--green) 70%, var(--green) 100%);
  }
  .back-rule { position: absolute; left: 121px; top: 0; bottom: 0; width: 2px; background: var(--blue); }
  .back-ring {
    position: absolute; left: 250px; top: -10px;
    width: 340px; height: 340px; border-radius: 50%;
    border: 44px solid var(--faint-back);
  }
  .back-brand {
    position: absolute; left: 48px; top: 37px; height: 94px;
    display: flex; align-items: center; gap: 16px;
    background: var(--white); padding-left: 14px; padding-right: 8px;
  }
  .back-brand .mark { width: 62px; height: 62px; background: var(--blue); }
  .back-brand .name {
    color: var(--ink); font-weight: 600; font-size: 27px;
    line-height: 1.05; letter-spacing: 3px; text-transform: uppercase;
  }
  .person { position: absolute; left: 128px; top: 142px; }
  .person .full-name { font-size: 21px; font-weight: 600; line-height: 1.2; }
  .person .first { color: var(--blue); }
  .person .last { color: var(--green); }
  .person .underline { width: 120px; height: 2px; background: var(--blue); margin: 2px 0 4px -4px; }
  .person .role { color: var(--green); font-size: 14px; font-weight: 600; }

  .contacts { position: absolute; left: 142px; top: 217px; list-style: none; }
  .contacts li {
    display: flex; align-items: center; gap: 12px;
    height: 32px; color: var(--ink); font-size: 13px; font-weight: 600;
  }
  .contacts svg { width: 18px; height: 18px; flex: none; }
</style>
</head>
<body>
<main class="sheet">

  <!-- Front, square corners -->
  <section class="card card--front" style="left:18px; top:110px;">
    <div class="front-ring"></div>
    <div class="front-brand">
      <span class="mark"></span>
      <p class="name">Velora<br>Pixel<br>Outreach</p>
    </div>
  </section>

  <!-- Back, square corners -->
  <section class="card card--back" style="left:612px; top:110px;">
    <div class="back-ring"></div>
    <div class="back-band"></div>
    <div class="back-rule"></div>
    <div class="back-brand">
      <span class="mark"></span>
      <p class="name">Velora<br>Pixel<br>Outreach</p>
    </div>
    <div class="person">
      <p class="full-name"><span class="first">Dermot</span> <span class="last">Kalway</span></p>
      <div class="underline"></div>
      <p class="role">Online Marketing Strategist</p>
    </div>
    <ul class="contacts">
      <li><svg viewBox="0 0 18 18"><rect width="18" height="18" rx="2" fill="#2fa9df"/><circle cx="9" cy="9" r="6" fill="none" stroke="#fff" stroke-width="1.3"/><ellipse cx="9" cy="9" rx="2.6" ry="6" fill="none" stroke="#fff" stroke-width="1.1"/><line x1="3" y1="9" x2="15" y2="9" stroke="#fff" stroke-width="1.1"/></svg>0492 158 620</li>
      <li><svg viewBox="0 0 18 18"><rect width="18" height="18" rx="2" fill="#2fa9df"/><rect x="3" y="5" width="12" height="8" fill="none" stroke="#fff" stroke-width="1.2"/><polyline points="3,5 9,10 15,5" fill="none" stroke="#fff" stroke-width="1.2"/></svg>Dermot@VeloraPixelOutreach.example</li>
      <li><svg viewBox="0 0 18 18"><rect width="18" height="18" rx="2" fill="#2fa9df"/></svg>in/dermotkalway</li>
    </ul>
  </section>

  <!-- Front, rounded corners -->
  <section class="card card--front card--rounded" style="left:18px; top:487px;">
    <div class="front-ring"></div>
    <div class="front-brand">
      <span class="mark"></span>
      <p class="name">Velora<br>Pixel<br>Outreach</p>
    </div>
  </section>

  <!-- Back, rounded corners -->
  <section class="card card--back card--rounded" style="left:612px; top:484px;">
    <div class="back-ring"></div>
    <div class="back-band"></div>
    <div class="back-rule"></div>
    <div class="back-brand">
      <span class="mark"></span>
      <p class="name">Velora<br>Pixel<br>Outreach</p>
    </div>
    <div class="person">
      <p class="full-name"><span class="first">Dermot</span> <span class="last">Kalway</span></p>
      <div class="underline"></div>
      <p class="role">Online Marketing Strategist</p>
    </div>
    <ul class="contacts">
      <li><svg viewBox="0 0 18 18"><rect width="18" height="18" rx="2" fill="#2fa9df"/><circle cx="9" cy="9" r="6" fill="none" stroke="#fff" stroke-width="1.3"/><ellipse cx="9" cy="9" rx="2.6" ry="6" fill="none" stroke="#fff" stroke-width="1.1"/><line x1="3" y1="9" x2="15" y2="9" stroke="#fff" stroke-width="1.1"/></svg>0492 158 620</li>
      <li><svg viewBox="0 0 18 18"><rect width="18" height="18" rx="2" fill="#2fa9df"/><rect x="3" y="5" width="12" height="8" fill="none" stroke="#fff" stroke-width="1.2"/><polyline points="3,5 9,10 15,5" fill="none" stroke="#fff" stroke-width="1.2"/></svg>Dermot@VeloraPixelOutreach.example</li>
      <li><svg viewBox="0 0 18 18"><rect width="18" height="18" rx="2" fill="#2fa9df"/></svg>in/dermotkalway</li>
    </ul>
  </section>

</main>
</body>
</html>
```